Business card design for a teacher - double sided, sleek design.

My name is Lina and I am an online Arabic language teacher. I am looking for a beautiful business card design for my online teaching business.

The cards will be printed in 85mm x 55mm size.
The card can be either portrait or landscape.

The design should contain my logo on one side and information on the other.

The design needs to be clean and modern. Use of subtle Arabic geometric patterns would be nice. Icons for the social media information on the card should also match the design theme.

My logo font is Consolas, which is a Monospace font.

Business card design should be delivered with editable PSD or EPS files in the handover.

Thanks

Lina

----

Information on the back:

URL: www.speakwithnadia.net [this should stand out more than other details]
Email: info@speakwithnadia.net
Instagram: @speakwithnadia
Facebook: circlepage.net/speakwithnadia
Skype: speakwithnadia

My brand colours are shown in the logo attached. These are:
- Teal green - 4DC9C1
- Mango yellow - FFD600

Target Market(s)

- Young professionals
- Expatriates
- Women and Men

Industry/Entity Type

Education

Contact Information for Business Card

Information on the back:

Skype: speakwithnadia

- Teal green - 4DC9C1
- Mango yellow - FFD600

Font styles to use
Other font styles liked:
• Any font complimentary to my logo font which is a Monospace font called Consolas.

Colors

Designer to choose colors to be used in the design.

Requirements
Must have
• - Aesthetically pleasing look
• - Complimentary design with existing logo
Nice to have
• Arabic geometrical patterns

```html
<!DOCTYPE html>
<html lang="en">
<head>
<meta charset="utf-8">
<title>Arabic with Lina – Business Card</title>
<link rel="stylesheet" href="https://fonts.googleapis.com/css2?family=Inconsolata:wght@400;700&display=swap">
<style>
  :root {
    --teal: #4dc9c1;
    --mango: #ffd600;
    --ink: #1e1e1e;
    --grey: #555a5e;
    --paper: #ffffff;
    --backdrop: #e9ebec;
  }
  * { box-sizing: border-box; margin: 0; padding: 0; }
  html, body { width: 1200px; height: 900px; overflow: hidden; }
  body {
    background: var(--backdrop);
    font-family: "Inconsolata", monospace;
    color: var(--ink);
    position: relative;
  }
  .card {
    position: absolute;
    top: 285px;
    width: 510px;
    height: 330px;
    background: var(--paper);
    box-shadow: 0 6px 18px rgba(0,0,0,.12);
    overflow: hidden;
  }
  .card--back { left: 60px; }
  .card--front { left: 630px; border: 18px solid var(--mango); }

  .brand__name {
    font-size: 30px;
    font-weight: 700;
    letter-spacing: 3px;
    color: var(--grey);
    text-transform: uppercase;
    line-height: 1;
    white-space: nowrap;
  }

  /* front */
  .card--front .brand__name {
    position: absolute; left: 0; right: 0; top: 112px;
    text-align: center;
  }
  .front__url {
    position: absolute; left: 0; right: 0; top: 178px;
    text-align: center;
    font-size: 17px; font-weight: 700; letter-spacing: 1px;
    color: var(--ink);
  }

  /* back */
  .card--back .brand__name { position: absolute; left: 110px; top: 50px; }
  .back__accent { position: absolute; inset: 0; width: 100%; height: 100%; }
  .contact { position: absolute; left: 110px; top: 120px; list-style: none; }
  .contact__item {
    display: flex; align-items: center; gap: 10px;
    font-size: 17px; color: var(--grey); line-height: 27px;
    white-space: nowrap;
  }
  .contact__icon { width: 15px; height: 15px; flex: none; }
  .contact__icon--plain { background: var(--teal); }
  .contact__item--url { font-size: 20px; font-weight: 700; color: var(--ink); margin-top: 2px; }
</style>
</head>
<body>

  <section class="card card--back" aria-label="Card back, contact details">
    <svg class="back__accent" viewBox="0 0 510 330" aria-hidden="true">
      <polygon points="0,140 14,140 14,300 40,330 0,330" fill="var(--mango)"/>
      <polygon points="150,302 510,302 510,330 176,330" fill="var(--teal)"/>
      <polygon points="14,300 150,302 176,330 40,330" fill="var(--teal)" opacity=".85"/>
    </svg>
    <p class="brand__name">Arabic with Lina</p>
    <ul class="contact">
      <li class="contact__item"><span class="contact__icon contact__icon--plain"></span>speakwithnadia</li>
      <li class="contact__item"><span class="contact__icon contact__icon--plain"></span>@speakwithnadia</li>
      <li class="contact__item"><span class="contact__icon contact__icon--plain"></span>circlepage.net/speakwithnadia</li>
      <li class="contact__item">
        <svg class="contact__icon" viewBox="0 0 16 16" aria-hidden="true">
          <rect width="16" height="16" fill="var(--teal)"/>
          <rect x="3" y="4.5" width="10" height="7" fill="none" stroke="#fff" stroke-width="1.3"/>
          <polyline points="3,4.5 8,9 13,4.5" fill="none" stroke="#fff" stroke-width="1.3"/>
        </svg>info@speakwithnadia.net
      </li>
      <li class="contact__item contact__item--url">
        <svg class="contact__icon" viewBox="0 0 16 16" aria-hidden="true">
          <rect width="16" height="16" fill="var(--teal)"/>
          <circle cx="8" cy="8" r="5" fill="none" stroke="#fff" stroke-width="1.2"/>
          <ellipse cx="8" cy="8" rx="2.2" ry="5" fill="none" stroke="#fff" stroke-width="1"/>
          <line x1="3" y1="8" x2="13" y2="8" stroke="#fff" stroke-width="1"/>
        </svg>www.speakwithnadia.net
      </li>
    </ul>
  </section>

  <section class="card card--front" aria-label="Card front, brand">
    <p class="brand__name">Arabic with Lina</p>
    <p class="front__url">www.speakwithnadia.net</p>
  </section>

</body>
</html>
```